Header/Banner Design

I need a website, youtube and Facebook header design all using a common theme.

The site will be called Harbor Lantern Advisor
The Header/Banners images must reflect the core feature of the website and social media pages, which is that the embedded AI Chatbot on the website is programmed with vast amounts of information and 20 years of human experience in the Time and Attendance Industry.

I imagine an image where an AI is absorbing information from software and documents and employees time clocks ( there are plenty of images of these on the web and some on another of my websites www.harborlantern.com.au)

```html
<!DOCTYPE html>
<html lang="en">
<head>
<meta charset="utf-8">
<title>Harbor Lantern Advisor – Header</title>
<link href="https://fonts.googleapis.com/css2?family=Montserrat:wght@500;600;700;800&display=swap" rel="stylesheet">
<style>
  :root {
    --hero-dark: #0a1214;
    --hero-teal: #1e3a3f;
    --hero-cyan: #3f7a80;
    --hero-panel: #9fb4b2;
    --hero-warm: #6b655d;
    --hero-light: #c9bfb0;
    --ink-white: #ffffff;
    --brand-blue: #6699cc;
    --body-grey: #555555;
    --logo-black: #111111;
    --page: #ffffff;
  }
  * { margin: 0; padding: 0; box-sizing: border-box; }
  html, body { width: 1200px; height: 675px; overflow: hidden; background: var(--page); }
  .banner {
    position: relative;
    width: 1200px;
    height: 675px;
    font-family: "Montserrat", sans-serif;
    background: var(--page);
  }
  .hero {
    position: absolute;
    left: 0; top: 0;
    width: 1200px; height: 509px;
    background:
      linear-gradient(180deg, rgba(0,0,0,0) 40%, rgba(4,8,10,0.85) 100%),
      radial-gradient(ellipse 240px 220px at 310px 190px, rgba(63,122,128,0.85) 0%, rgba(30,58,63,0) 100%),
      radial-gradient(ellipse 110px 170px at 610px 160px, rgba(159,180,178,0.75) 0%, rgba(93,102,100,0) 100%),
      radial-gradient(ellipse 170px 260px at 890px 230px, rgba(107,101,93,0.6) 0%, rgba(40,38,36,0) 100%),
      linear-gradient(90deg, var(--hero-teal) 0%, #18302f 40%, #101b1d 62%, var(--hero-dark) 72%, #2a2927 88%, var(--hero-light) 100%);
  }
  .hero-headline {
    position: absolute;
    left: 0; top: 306px;
    width: 1200px;
    text-align: center;
    color: var(--ink-white);
    font-weight: 500;
    font-size: 36px;
    line-height: 51px;
    letter-spacing: -0.4px;
  }
  .brand-mark {
    position: absolute;
    left: 68px; top: 546px;
    width: 186px;
    text-align: center;
  }
  .brand-mark .dot {
    display: block;
    margin: 0 auto;
    width: 80px; height: 80px;
    border-radius: 50%;
    border: 3px solid var(--brand-blue);
  }
  .brand-mark .name {
    display: block;
    margin-top: 9px;
    font-weight: 800;
    font-size: 11.5px;
    color: var(--logo-black);
    white-space: nowrap;
  }
  .intro {
    position: absolute;
    left: 293px; top: 546px;
    width: 350px;
  }
  .intro-title {
    font-weight: 700;
    font-size: 23px;
    color: var(--brand-blue);
    letter-spacing: 0.2px;
    white-space: nowrap;
  }
  .intro-text {
    margin-top: 16px;
    font-weight: 500;
    font-size: 13.5px;
    line-height: 21px;
    color: var(--body-grey);
  }
  .contact-button {
    position: absolute;
    left: 873px; top: 561px;
    width: 221px; height: 64px;
    border-radius: 32px;
    background: var(--brand-blue);
    color: var(--ink-white);
    font-weight: 700;
    font-size: 22px;
    letter-spacing: 0.5px;
    display: flex;
    align-items: center;
    justify-content: center;
    text-decoration: none;
  }
</style>
</head>
<body>
  <div class="banner">
    <div class="hero" role="img" aria-label="Photo of an AI robot head and a young man facing a glowing document on a screen, in dark teal tones"></div>
    <h1 class="hero-headline">WE ARE COMMITTED TO IMPROVING<br>YOUR EMPLOYEE ATTENDANCE RECORDING<br>AND REDUCING YOUR PAYROLL COSTS</h1>

    <div class="brand-mark">
      <span class="dot"></span>
      <span class="name">HARBOR LANTERN ADVISOR</span>
    </div>

    <div class="intro">
      <h2 class="intro-title">HARBOR LANTERN ADVISOR</h2>
      <p class="intro-text">We Are Committed To Improving Your Employee Attendance Recording and&nbsp; Reducing Your&nbsp; Payroll Costs</p>
    </div>

    <a class="contact-button" href="#">CONTACT US</a>
  </div>
</body>
</html>
```